Poster Design Project

We are youth orchestra in Texas that is introducing a new summer program called: Weekend Bows Holiday Program (It's for students ages 8-18 who play already play violin/viola/cello/bass

Poster size: 11" by 17"

All the details are below, but on the poster we would need the website listed: www.marlowridgejuniorensemble.example and tell them to go to that website to apply online beginning April 1st

That's how we get business, they go to our website and apply. It also needs to say really big MRJE WEEKEND BOWS HOLIDAY PROGRAM

We want to use these posters every summer so no dates on it please. Only: April 1st is when we being accepting online applications (every year, so don't put a year) Also put: Camp is held on Saturdays in June and July with final concert, last Sunday in July

Also on the poster we need: Our goal is to keep young musicians playing over the summer –so don’t put your instrument away for the summer! Keep in shape by joining us for the Marlow Ridge Junior Ensemble’s summer program – Weekend Bows Holiday Program! Tuition is $225, which covers June/July Saturday rehearsals and the performance fee for the BVSD FAH concert, last Sunday in July.

I know we can't get all the info below on it, but I put it on so you could better understand what we are doing.

We have a logo already, that we have the rights to - I need something that kids/teens will think is cool looking and music related....we are string instruments only (violin, viola, cello, bass) we also want it to look classy looking, not cheap
I included 2 copies of the logo in different color set

here's all the details from our website:
Weekend Bows Holiday Program (June and July) - Tuition: $225

Rehearsals on Saturdays June &July with final concert on last Sunday in July @ BHS FAH

Our goal is to keep young musicians playing over the summer –so don’t put your instrument away for the summer! Keep in shape by joining us for the Marlow Ridge Junior Ensemble’s new summer program – Weekend Bows Holiday Program!

Tuition is $225, which covers June/July Saturday rehearsals and the performance fee for the BVSD FAH concert.

No audition is necessary. Enrollment is limited to the first 50 students in each age category, depending on instrumentation needs, so don’t delay – enrollment online begins April 1st. Siblings will receive a $50 discount, after the first child's regular priced tuition.

Weekend Bows I: Students entering grades 6 and below (3:00 – 4:20 P.M. )
Weekend Bows II: Students grades entering 7 and 8 (4:30 – 6:00 P.M.)
Weekend Bows III: Students entering grades 9-12 (6:15 – 7:45 P.M.)

Summer camp attendance policy is more lenient due to summer vacations. Please notify MRJE of summer absences as soon as your vacation/camp dates are known.

Target Market(s)

string players ages 10-18 and their parents

Industry/Entity Type

Business

Requirements
Must have
• Be able to see title from far, and prominently display how/when to apply and where (website)

Also only the concert is at BHS FAH, we rehearse at Harbel Music in Allen

I'm working on uploading files for our QR codes for website and phone - It's uploaded below
Nice to have
• If you have room, the Weekend Holiday Bows I II and III times/grades, etc. but doesn't have to be seen as prominently as the title and how to apply
Should not have
• pictures of violin/vla/cello/bass students if they look elementary aged, should be more in the teenager age group if you use pictures.

```html
<!DOCTYPE html>
<html lang="en">
<head>
<meta charset="utf-8">
<title>MRJE Weekend Bows Holiday Program</title>
<link rel="stylesheet" href="https://fonts.googleapis.com/css2?family=Cabin+Sketch:wght@700&family=Jost:ital,wght@0,400;0,600;1,400;1,600&family=Nunito:wght@900&family=Schoolbell&display=swap">
<style>
  :root {
    --parchment-light: #f3e2b4;
    --parchment-mid: #e6c98c;
    --parchment-deep: #c9a463;
    --wood-light: #b2542a;
    --wood-dark: #5a1c0c;
    --ink: #1c1712;
    --ink-soft: #2b241c;
    --title-white: #ffffff;
  }
  * { margin: 0; padding: 0; box-sizing: border-box; }
  html, body { width: 776px; height: 1200px; overflow: hidden; }
  body { background: var(--parchment-light); }

  .poster {
    position: relative;
    width: 776px;
    height: 1200px;
    overflow: hidden;
    background:
      radial-gradient(ellipse at 55% 78%, var(--parchment-light) 0%, var(--parchment-mid) 60%, var(--parchment-deep) 100%);
    font-family: "Jost", "Futura", sans-serif;
    color: var(--ink);
  }

  .instrument-photo {
    position: absolute;
    left: 0; top: 0;
    width: 776px; height: 640px;
  }

  .intro {
    position: absolute;
    left: 37px; top: 420px;
    width: 500px;
    font-size: 17.5px;
    line-height: 1.35;
    color: var(--ink-soft);
  }
  .intro p + p { margin-top: 8px; }
  .intro strong { font-weight: 600; color: var(--ink); }

  .title-main {
    position: absolute;
    left: 0; top: 680px; width: 776px;
    text-align: center;
    font-family: "Nunito", "Arial Rounded MT Bold", sans-serif;
    font-weight: 900;
    font-size: 52px;
    letter-spacing: 0.5px;
    color: var(--title-white);
    text-shadow: 2px 3px 4px rgba(40, 25, 10, 0.75);
  }
  .title-sub {
    position: absolute;
    left: 0; top: 764px; width: 776px;
    text-align: center;
    font-family: "Cabin Sketch", "Impact", cursive;
    font-weight: 700;
    font-size: 70px;
    letter-spacing: 4px;
    color: var(--ink);
  }

  .website {
    position: absolute;
    left: 0; top: 866px; width: 776px;
    text-align: center;
    font-size: 29px;
    color: var(--ink);
  }
  .website .domain { font-weight: 400; color: var(--ink); letter-spacing: 0.2px; }

  .apply-note {
    position: absolute;
    left: 0; top: 918px; width: 776px;
    text-align: center;
    font-size: 16px;
    color: var(--ink-soft);
  }
  .apply-cta {
    position: absolute;
    left: 0; top: 946px; width: 776px;
    text-align: center;
    font-family: "Schoolbell", cursive;
    font-size: 30px;
    letter-spacing: 1px;
    color: var(--ink);
  }

  .sessions {
    position: absolute;
    left: 37px; top: 1008px;
    list-style: none;
    font-style: italic;
    font-size: 16.5px;
    line-height: 1.22;
    color: var(--ink-soft);
  }
  .sessions li + li { margin-top: 6px; }
  .sessions .session-name { display: block; font-weight: 600; color: var(--ink); }

  .org-mark {
    position: absolute;
    left: 470px; top: 1098px;
    display: flex; align-items: center; gap: 12px;
  }
  .org-mark .dot {
    width: 34px; height: 34px; border-radius: 50%;
    background: var(--ink);
  }
  .org-mark .name {
    font-family: "Jost", "Futura", sans-serif;
    font-weight: 600;
    font-size: 52px;
    color: var(--ink);
    letter-spacing: 1px;
  }
</style>
</head>
<body>
<main class="poster">
  <svg class="instrument-photo" viewBox="0 0 776 640" role="img" aria-label="Close-up photograph of a violin body with strings, bridge and f-holes lying diagonally across aged parchment">
    <defs>
      <linearGradient id="wood" x1="0" y1="0" x2="1" y2="1">
        <stop offset="0" stop-color="#7a2a12"/>
        <stop offset="0.45" stop-color="#b2542a"/>
        <stop offset="1" stop-color="#5a1c0c"/>
      </linearGradient>
    </defs>
    <path d="M0 0 H776 V640 C740 610 700 520 640 470 C600 440 560 400 520 370 C480 330 420 300 360 300 C300 300 250 340 200 330 C130 320 60 280 0 250 Z" fill="url(#wood)"/>
  </svg>

  <section class="intro">
    <p>Our goal is to keep young musicians playing over the summer - <strong>so don’t put your instrument away for the summer!</strong> Keep in shape by joining us for the Marlow Ridge Junior Ensemble’s summer program - Weekend Bows Holiday Program!</p>
    <p>Tuition: 225 June/July Saturday rehearsals at Harbel Music in Allen, final concert last sunday in July at BHS FAH.</p>
  </section>

  <h1>
    <span class="title-main">MRJE WEEKEND BOWS</span>
    <span class="title-sub">HOLIDAY PROGRAM</span>
  </h1>

  <p class="website">www.<span class="domain">marlowridgejuniorensemble</span>.example</p>
  <p class="apply-note">we open applications online or begin accepting them April 1st</p>
  <p class="apply-cta">apply online</p>

  <ul class="sessions">
    <li><span class="session-name">Weekend Bows I</span>High School players (3:00 - 4:20 P.M.)</li>
    <li><span class="session-name">Weekend Bows II</span>Middle School (4:30 - 6:00 P.M.),</li>
    <li><span class="session-name">Weekend Bows III</span>Elementary School (6:15 - 7:45 P.M.)</li>
  </ul>

  <div class="org-mark">
    <span class="dot"></span>
    <span class="name">MRJE</span>
  </div>
</main>
</body>
</html>
```